Creative, Colorful, Dynamic Infographic for Global Non-Profit

We are a global arts and education non-profit in need of an infographic that illustrates four key skills embedded in our work: Curiosity, Listening, Imagination, Postive Action.
We work primarily with educators, students, and artists who use the power of personal stories to build community and connection and to bridge divides.
Our new brand guidelines, logos, and fonts are here: https://stylevault.example/lumen-circle
I've attached a mock-up of the graphic and the required text. (Note the attached design was created by a staff person, your final design does not need to be the same. The color scheme and text of the final design should match the brand guidelines above.)
The graphic will be used for both web and print media and should include the purple Lumen Circle logo (also attached).
Ideally the final design will delight audiences and spark interest in our work.

```html
<!DOCTYPE html>
<html lang="en">
<head>
<meta charset="utf-8">
<title>Lumen Circle – Four Skills</title>
<link href="https://fonts.googleapis.com/css2?family=Libre+Franklin:wght@400;600;700&display=swap" rel="stylesheet">
<style>
  :root {
    --teal: #9ad5cb;
    --orange: #ffc477;
    --lavender: #d3bcd3;
    --coral: #ff9080;
    --purple: #663399;
    --ink: #333333;
    --paper: #fdfdfd;
    --white: #ffffff;
  }
  html, body {
    margin: 0;
    padding: 0;
    width: 1200px;
    height: 1200px;
    overflow: hidden;
    background: var(--paper);
  }
  .skills-graphic {
    display: block;
    width: 1200px;
    height: 1200px;
    font-family: "Libre Franklin", "Helvetica Neue", Arial, sans-serif;
  }
  .petal--teal, .quad--teal, .ring--teal, .badge--teal { fill: var(--teal); }
  .petal--orange, .quad--orange, .ring--orange, .badge--orange { fill: var(--orange); }
  .petal--lavender, .quad--lavender, .ring--lavender, .badge--lavender { fill: var(--lavender); }
  .petal--coral, .quad--coral, .ring--coral, .badge--coral { fill: var(--coral); }
  .ring { stroke: var(--white); stroke-width: 6; }
  .ring-inner { fill: var(--white); }
  .arrow { fill: var(--white); }
  .skill-text, .link-text {
    fill: var(--ink);
    font-size: 20.5px;
    text-anchor: middle;
    letter-spacing: 0.2px;
  }
  .skill-title { font-weight: 700; }
  .brand-disc { fill: var(--purple); stroke: var(--white); stroke-width: 5; }
  .brand-name {
    fill: var(--white);
    font-size: 19px;
    font-weight: 600;
    text-anchor: middle;
  }
</style>
</head>
<body>
<svg class="skills-graphic" viewBox="0 0 1200 1200" xmlns="http://www.w3.org/2000/svg" role="img" aria-label="Cycle of four skills: Curiosity, Listening, Imagination and Positive action">
  <!-- petals -->
  <ellipse class="petal--orange" cx="600" cy="300" rx="152" ry="111"/>
  <ellipse class="petal--teal" cx="299" cy="600" rx="111" ry="152"/>
  <ellipse class="petal--lavender" cx="901" cy="600" rx="111" ry="152"/>
  <ellipse class="petal--coral" cx="600" cy="900" rx="152" ry="111"/>

  <!-- centre quadrants -->
  <rect class="quad--teal" x="470" y="470" width="130" height="130"/>
  <rect class="quad--orange" x="600" y="470" width="130" height="130"/>
  <rect class="quad--coral" x="470" y="600" width="130" height="130"/>
  <rect class="quad--lavender" x="600" y="600" width="130" height="130"/>

  <!-- skill rings -->
  <circle class="ring ring--teal" cx="434" cy="434" r="148"/>
  <circle class="ring-inner" cx="434" cy="434" r="126"/>
  <circle class="ring ring--orange" cx="766" cy="434" r="148"/>
  <circle class="ring-inner" cx="766" cy="434" r="126"/>
  <circle class="ring ring--coral" cx="434" cy="766" r="148"/>
  <circle class="ring-inner" cx="434" cy="766" r="126"/>
  <circle class="ring ring--lavender" cx="766" cy="766" r="148"/>
  <circle class="ring-inner" cx="766" cy="766" r="126"/>

  <!-- flow badges -->
  <g class="flow-badge">
    <rect class="badge--orange ring" x="594" y="403" width="82" height="62" rx="10"/>
    <path class="arrow" d="M615 434 L632 417 L637 422 L629 430 L656 430 L656 438 L629 438 L637 446 L632 451 Z"/>
  </g>
  <g class="flow-badge">
    <rect class="badge--teal ring" x="405" y="525" width="62" height="82" rx="10"/>
    <path class="arrow" d="M434 586 L417 569 L422 564 L430 572 L430 546 L438 546 L438 572 L446 564 L451 569 Z"/>
  </g>
  <g class="flow-badge">
    <rect class="badge--coral ring" x="525" y="734" width="82" height="62" rx="10"/>
    <path class="arrow" d="M586 766 L569 783 L564 778 L572 770 L546 770 L546 762 L572 762 L564 754 L569 749 Z"/>
  </g>
  <g class="flow-badge">
    <rect class="badge--lavender ring" x="736" y="593" width="62" height="82" rx="10"/>
    <path class="arrow" d="M767 614 L784 631 L779 636 L771 628 L771 654 L763 654 L763 628 L755 636 L750 631 Z"/>
  </g>

  <!-- brand mark -->
  <g class="brand">
    <circle class="brand-disc" cx="600" cy="602" r="76"/>
    <text class="brand-name" x="600" y="598">Lumen<tspan x="600" dy="23">Circle</tspan></text>
  </g>

  <!-- skill descriptions -->
  <text class="skill-text" x="434" y="390">
    <tspan class="skill-title" x="434">Curiosity –</tspan>
    <tspan x="434" dy="26.5">Focus on how you can</tspan>
    <tspan x="434" dy="26.5">learn from another's</tspan>
    <tspan x="434" dy="26.5">knowledge and</tspan>
    <tspan x="434" dy="26.5">experience</tspan>
  </text>
  <text class="skill-text" x="773" y="390">
    <tspan class="skill-title" x="773">Positive action -</tspan>
    <tspan x="773" dy="26.5">Show your words</tspan>
    <tspan x="773" dy="26.5">and actions</tspan>
    <tspan x="773" dy="26.5">matter</tspan>
  </text>
  <text class="skill-text" x="433" y="734">
    <tspan class="skill-title" x="433">Listening –</tspan>
    <tspan x="433" dy="26.5">Seek to</tspan>
    <tspan x="433" dy="26.5">understand</tspan>
    <tspan x="433" dy="26.5">before speaking</tspan>
  </text>
  <text class="skill-text" x="766" y="734">
    <tspan class="skill-title" x="766">Imagination –</tspan>
    <tspan x="766" dy="26.5">Consider</tspan>
    <tspan x="766" dy="26.5">possibilities beyond</tspan>
    <tspan x="766" dy="26.5">what you know</tspan>
  </text>

  <!-- link descriptions -->
  <text class="link-text" x="602" y="259">
    <tspan x="602">Your positive actions</tspan>
    <tspan x="602" dy="26.5">lead to curiosity</tspan>
    <tspan x="602" dy="26.5">about what else</tspan>
    <tspan x="602" dy="26.5">is possible</tspan>
  </text>
  <text class="link-text" x="289" y="580">
    <tspan x="289">Your curiosity</tspan>
    <tspan x="289" dy="26.5">allows you</tspan>
    <tspan x="289" dy="26.5">to listen</tspan>
  </text>
  <text class="link-text" x="927" y="580">
    <tspan x="927">Your imagination</tspan>
    <tspan x="927" dy="26.5">can spark</tspan>
    <tspan x="927" dy="26.5">positive action</tspan>
  </text>
  <text class="link-text" x="602" y="894">
    <tspan x="602">Your listening</tspan>
    <tspan x="602" dy="26.5">allows you to</tspan>
    <tspan x="602" dy="26.5">take in new</tspan>
    <tspan x="602" dy="26.5">information</tspan>
  </text>
</svg>
</body>
</html>
```